Dashboard Elements

Hello – looking for someone to create dashboard elements.
I’ve already basically designed all these elements – but I need someone to take what I’ve designed and make it look like an actual dashboard UI, like an app - assuming using some kind of dashboard UI kit (but however you would like to get it done is fine). It can look just like mine or try something different, as long as it matches the color scheme webpage that I’m going to out it on – see the page here. I’m ok with making it dark, maybe that would look better – again as long as it matches the webpage (https://www.plandeck.io/file/7QxKtr2BwLpZnVe4Hs8Mc1/Webpage-with-placeholders?node-id=0%3A1). Please note, you do not need to put anything on the webpage or do anything with this Figma file, this is just a reference so you can color/stylize it accordingly.

The attached Powerpoint file has everything you need - make sure to zoom all the way out to see everything on the slides.

Here are the Dashboard elements needed (this will all make sense when you look at the PPT):
Dashboard 1
Dashboard 1 – expanded view A
Dashboard 1 – expanded view B
View Source button by itself
Source Document Viewer 1 and 2 (these are exactly the same just with a different image inside)*
Dashboard 2 (only slightly different than Dashboard 1, just extended with extra headings
Table of Contents
Searchbar and Source Doc by itself
*the documents in the source document viewers should still look like documents - they don’t need to look like part of the UI, because this is a document viewer – you can restyle/recolor if necessary or just leave these as is.
- Colors must match color scheme of webpage, attached and on Figma link (images there currently are only placeholders) – ok to go dark as long as it matches
- Must look sleek, clean, realistic
- Don’t add any pictures of people or change the text.
- In case it’s not clear, this is what I mean by the concept of Dashboard UI - https://www.notavia.net/shard/s7/sh/8fad21bc-14e9-4a7c-b2d0-5c3e9f71a604/92c4e1b7a05d3f68e1c2b947d0a3f815
- Must be sent in an editable file, I may need to be edit text and other elements
- If you are going to send a sample, please make sure it’s part of the dashboard itself, not just the table of contents etc

Ideally hoping to find someone I can continue working with as I'll have a lot more graphic design work needed coming up.

Thank you!

```html
<!DOCTYPE html>
<html lang="en">
<head>
<meta charset="utf-8">
<title>Compendium C-CDA – Summarized and Linked</title>
<link href="https://fonts.googleapis.com/css2?family=Rajdhani:wght@300;400;500&family=Roboto:wght@300;400&family=Roboto+Condensed:wght@400;700&family=Arimo:wght@400;700&family=Courier+Prime&display=swap" rel="stylesheet">
<style>
:root{
  --bg:#150f2f;
  --bg-deep:#0f0b24;
  --panel-top:#3a2f77;
  --panel-bot:#5a4aa6;
  --panel-edge:#7a68c8;
  --teal:#22c8c2;
  --teal-deep:#148f93;
  --teal-soft:#4fe0d6;
  --text:#e9e6f7;
  --text-dim:#c9c3e6;
  --paper:#ffffff;
  --ink:#222;
}
*{box-sizing:border-box;margin:0;padding:0}
html,body{width:1200px;height:3200px;overflow:hidden;background:var(--bg)}
body{position:relative;font-family:"Roboto",sans-serif;color:var(--text)}
.canvas{position:absolute;inset:0;overflow:hidden;
  background:
    radial-gradient(520px 420px at 1230px 80px, rgba(120,90,220,.55), transparent 70%),
    radial-gradient(380px 320px at -40px 900px, rgba(30,150,160,.45), transparent 70%),
    radial-gradient(360px 300px at 1230px 880px, rgba(40,190,170,.45), transparent 70%),
    radial-gradient(420px 360px at -60px 1500px, rgba(110,80,200,.35), transparent 70%),
    radial-gradient(500px 400px at 1240px 2350px, rgba(110,80,210,.45), transparent 70%),
    radial-gradient(420px 380px at -40px 2450px, rgba(70,60,170,.35), transparent 70%),
    linear-gradient(180deg,var(--bg-deep),var(--bg) 40%,#1a1340 100%);}
.abs{position:absolute}

/* intro */
.intro-tail{left:615px;top:-10px;width:500px;font-size:17px;line-height:27px;font-weight:300;color:var(--text-dim)}
.art-fill{border-radius:40px}
.art-top{left:60px;top:0;width:480px;height:200px;
  background:radial-gradient(60% 80% at 40% 20%,rgba(60,50,130,.55),rgba(30,110,150,.25) 60%,transparent 100%)}
.art-network{left:580px;top:160px;width:225px;height:580px;
  background:radial-gradient(70% 50% at 50% 45%,rgba(60,50,130,.5),rgba(30,140,170,.2) 60%,transparent 100%)}
.section-label{left:86px;top:348px;font-family:"Rajdhani",sans-serif;font-weight:500;font-size:19px;letter-spacing:1.6px;color:var(--text)}
.section-copy{left:86px;top:390px;width:388px;font-size:16.5px;line-height:27px;font-weight:300;color:var(--text-dim)}
.ccda-chip{left:703px;top:356px;width:89px;height:41px;border-radius:6px;background:linear-gradient(180deg,#1b9fae,#177c94);
  border:1px solid var(--teal-soft);box-shadow:0 0 14px rgba(40,210,210,.45);
  font-family:"Rajdhani",sans-serif;font-size:19px;letter-spacing:1px;display:flex;align-items:center;justify-content:center;color:#dff}

/* table of contents */
.toc{left:817px;top:186px;width:204px;height:472px;border-radius:6px;
  background:linear-gradient(180deg,#4a3c98,#5c4cae);border:1px solid var(--panel-edge);box-shadow:0 0 24px rgba(140,110,240,.35)}
.toc-head{position:absolute;left:0;top:0;right:0;height:42px;border-radius:6px 6px 0 0;background:linear-gradient(180deg,#564aa8,#3e3386);display:flex;align-items:center;padding-left:10px}
.toc-head span{display:block;width:186px;height:26px;border-radius:3px;background:linear-gradient(90deg,var(--teal),#1aa7a9);
  font-family:"Roboto Condensed",sans-serif;font-weight:700;font-size:11.5px;line-height:26px;padding-left:26px;color:#fff;box-shadow:0 0 10px rgba(40,220,210,.5)}
.toc-rail{position:absolute;top:60px;bottom:18px;width:4px;background:var(--teal);border-radius:2px;box-shadow:0 0 8px var(--teal)}
.toc-list{position:absolute;left:10px;right:10px;top:67px;list-style:none}
.toc-list li{height:36.8px;border-bottom:1px solid rgba(60,200,200,.45);font-family:"Roboto Condensed",sans-serif;font-weight:700;font-size:11.5px;
  line-height:36px;padding-left:26px;color:#fff}
.toc-list li.is-active{background:linear-gradient(90deg,var(--teal),#1aa7a9);border-radius:3px;height:32px;line-height:32px;margin-bottom:4px;border:none}

/* summary box */
.summary-box{left:82px;top:741px;width:1036px;height:595px;border-radius:14px;border:1px solid rgba(170,160,220,.35);
  background:linear-gradient(180deg,rgba(40,34,80,.55),rgba(30,24,66,.35))}
.summary-title{left:0;width:1200px;top:808px;text-align:center;font-family:"Rajdhani",sans-serif;font-weight:300;font-size:44px;line-height:51px;letter-spacing:3.5px;color:#fff}
.summary-copy{left:0;width:1200px;top:933px;text-align:center;font-size:16.5px;line-height:27.5px;font-weight:300;color:var(--text-dim)}

/* dashboard panel */
.panel{border-radius:6px;background:linear-gradient(180deg,var(--panel-top),var(--panel-bot));
  border:1px solid var(--panel-edge);box-shadow:0 0 34px rgba(140,110,240,.45),inset 0 0 0 4px rgba(40,30,90,.35)}
.panel::before,.panel::after{content:"";position:absolute;top:22%;height:52%;width:4px;border-radius:2px;background:var(--teal);box-shadow:0 0 10px var(--teal)}
.panel::before{left:-2px}.panel::after{right:-2px}
.cond{font-family:"Roboto Condensed",sans-serif}
.brand{display:flex;align-items:center;gap:6px;font-family:"Rajdhani",sans-serif;font-size:16px;letter-spacing:.8px;color:#fff}
.brand i{display:block;width:12px;height:12px;background:var(--teal-soft)}
.doc-title{font-family:"Roboto Condensed",sans-serif;font-weight:700;font-size:12.5px;color:#fff}
.patient{text-align:right;font-family:"Roboto Condensed",sans-serif;font-weight:700;font-size:11px;line-height:15px;color:#fff}
.patient b{color:var(--teal-soft);font-weight:400}
.patient .who{display:inline-flex;align-items:center;gap:6px}
.caret{display:inline-block;width:0;height:0;border-left:7px solid transparent;border-right:7px solid transparent;border-top:8px solid var(--teal)}
.caret.sm{border-left-width:5px;border-right-width:5px;border-top-width:6px}
.caret.up{border-top:none;border-bottom:6px solid var(--teal)}
.pill{border-radius:3px;background:linear-gradient(90deg,var(--teal-deep),var(--teal));border:1px solid var(--teal-soft);
  box-shadow:0 0 10px rgba(40,220,210,.45);font-family:"Roboto Condensed",sans-serif;font-weight:700;font-size:11px;color:#fff;
  display:flex;align-items:center;justify-content:center}
.btn-source{border-radius:3px;background:linear-gradient(180deg,#3434a2,#262683);border:1px solid #6f7ae0;box-shadow:0 0 10px rgba(90,110,240,.5);
  font-family:"Roboto Condensed",sans-serif;font-weight:700;font-size:11px;color:#fff;display:flex;align-items:center;justify-content:center;gap:7px}
.btn-source svg{width:13px;height:13px}

.hcc-table{position:absolute;left:25px;right:25px;top:137px}
.hcc-head{height:50px;border-radius:3px;background:linear-gradient(90deg,#1a9aa1,var(--teal) 60%,#1aa7a9);box-shadow:0 0 12px rgba(40,220,210,.45);
  position:relative;font-family:"Roboto Condensed",sans-serif;font-weight:700;font-size:10.5px;color:#fff}
.hcc-row{position:relative;height:45.5px;border-bottom:1px solid rgba(60,200,200,.55);font-family:"Roboto Condensed",sans-serif;font-weight:700;font-size:10.5px;color:#fff}
.hcc-row > *,.hcc-head > *{position:absolute;top:50%;transform:translateY(-50%)}
.c-code{left:10px}.c-cond{left:105px}.c-cat{left:368px}.c-raf{left:426px}.c-chev{left:470px}
.hcc-row .c-code,.hcc-row .c-cat{color:var(--teal-soft);font-weight:400}

/* expanded */
.x-item{font-family:"Roboto Condensed",sans-serif;font-weight:700;font-size:10.5px;line-height:12px;color:#fff}
.strip{background:linear-gradient(90deg,#138a93,var(--teal) 50%,#1aa7a9);border:1px solid var(--teal-soft);box-shadow:0 0 18px rgba(40,220,210,.55);border-radius:2px}
.strip .x-item{position:absolute;top:50%;transform:translateY(-50%)}
.strip .detail{font-weight:400}
.glow-bar{height:7px;border-radius:4px;background:var(--teal);box-shadow:0 0 12px var(--teal)}

.icon-ring{width:62px;height:62px;border-radius:50%;border:1px solid rgba(140,120,220,.55);display:flex;align-items:center;justify-content:center}
.icon-ring svg{width:30px;height:30px}
.vline{width:1px;background:rgba(140,120,220,.45)}

/* documents */
.doc-panel .docs-label{position:absolute;left:26px;top:92px;display:flex;gap:10px;align-items:center;font-family:"Roboto Condensed",sans-serif;font-weight:700;font-size:11.5px;color:#fff}
.page{background:var(--paper);color:var(--ink);font-family:"Arimo",sans-serif;font-size:7.2px;line-height:9px;overflow:hidden}
.page .muted{color:#777}
.page .row{display:flex}
.page .k{width:88px}
.page .sec{margin-top:8px;color:#888}
.page table{border-collapse:collapse;width:100%;font-size:6.6px}
.page td,.page th{text-align:left;padding:0 2px;font-weight:400}
.page th{font-weight:700}
.boxed{border:1px solid #666}
.mono{font-family:"Courier Prime",monospace;font-size:6.8px;line-height:8px}
.hl{background:#7fe3de}
</style>
</head>
<body>
<div class="canvas">

  <!-- intro -->
  <div class="abs art-fill art-top" role="img" aria-label="Decorative data-flow artwork with a large ring and glowing node"></div>
  <p class="abs intro-tail">techniques. Clinical Natural Language Processing (CNLP), proprietary logic and NPI matching to clean, de-duplicate, structure and enrich all inputs from data acquisition.</p>

  <div class="abs art-fill art-network" role="img" aria-label="Decorative network artwork linking data nodes to a C-CDA document"></div>

  <h3 class="abs section-label">COMPENDIUM C-CDA</h3>
  <p class="abs section-copy">The normalized data is unified into the Compendium C-CDA. Enhanced composite longitudinal record in C-CDA format, the industry standard for all interoperability initiatives.</p>
  <div class="abs ccda-chip">C-CDA</div>

  <nav class="abs toc" aria-label="Table of contents">
    <div class="toc-head"><span>Table of contents</span></div>
    <div class="toc-rail" style="left:8px"></div>
    <div class="toc-rail" style="right:8px"></div>
    <ul class="toc-list">
      <li class="is-active">Insurance providers</li>
      <li>Problems</li><li>Results</li><li>Procedures</li><li>Encounters</li><li>Medications</li>
      <li>Vital signs</li><li>Immunizations</li><li>Social history</li><li>Family history</li><li>Plan of Care</li>
    </ul>
  </nav>

  <!-- summary -->
  <div class="abs summary-box"></div>
  <h2 class="abs summary-title">SUMMARIZED AND LINKED<br>TO KEY INSIGHTS</h2>
  <p class="abs summary-copy">Insights are presented in a concise summary with direct links to supporting evidence.<br>HCC opportunities are abstracted and cross-linked directly to the original text in the<br>underlying record for quick and easy reference.</p>

  <!-- dashboard: HCC summary -->
  <section class="abs panel hcc-panel" style="left:325px;top:1105px;width:541px;height:420px">
    <div class="abs brand" style="left:24px;top:33px"><i></i>CLINIVIEW</div>
    <div class="abs doc-title" style="left:215px;top:34px">C-CDA Compendium</div>
    <div class="abs patient" style="right:20px;top:28px">
      <span class="who"><svg width="12" height="12" viewBox="0 0 12 12"><circle cx="6" cy="4" r="3" fill="#fff"/><path d="M1 12c0-3 2.5-4.5 5-4.5s5 1.5 5 4.5z" fill="#fff"/></svg>Patient, Mary</span><br>
      <b>Female</b> | 01/11/1951 | <b>Age: 70</b>
    </div>
    <div class="abs cond" style="left:32px;top:97px;display:flex;gap:14px;align-items:center;font-weight:700;font-size:11px;color:#fff"><span class="caret"></span>HCC Summary</div>
    <div class="abs pill" style="left:259px;top:89px;width:256px;height:32px">RAF: 2.362 | Condition Count: 8 | ID: 7326472</div>
    <div class="hcc-table">
      <div class="hcc-head"><span class="c-code">ICD-10 Code</span><span class="c-cond">Condition</span><span class="c-cat">Category</span><span class="c-raf">RAF</span></div>
      <div class="hcc-row"><span class="c-code">J44.9</span><span class="c-cond">Chronic obstructive pulmonary disease</span><span class="c-cat">111</span><span class="c-raf">0.335</span><span class="c-chev caret sm"></span></div>
      <div class="hcc-row"><span class="c-code">F33.1</span><span class="c-cond">Chronic kidney disease, moderate (stage 3)</span><span class="c-cat">138</span><span class="c-raf">0.069</span><span class="c-chev caret sm"></span></div>
      <div class="hcc-row"><span class="c-code">F33.0</span><span class="c-cond">Major depressive disorder, recurrent, mild</span><span class="c-cat">59</span><span class="c-raf">0.309</span><span class="c-chev caret sm"></span></div>
      <div class="hcc-row"><span class="c-code">I42.9</span><span class="c-cond">Cardiomyopathy</span><span class="c-cat">85</span><span class="c-raf">0.447</span><span class="c-chev caret sm"></span></div>
      <div class="hcc-row" style="border-bottom:none"><span class="c-code">E11.36</span><span class="c-cond">Type 2 diabetes mellitus with diabetic cataract</span><span class="c-cat">18</span><span class="c-raf">0.302</span><span class="c-chev caret sm"></span></div>
    </div>
  </section>

  <!-- dashboard: expanded -->
  <section class="abs panel expanded-panel" style="left:325px;top:1625px;width:541px;height:430px">
    <div class="abs glow-bar" style="left:160px;right:160px;top:-3px"></div>
    <div class="abs glow-bar" style="left:160px;right:160px;bottom:-3px"></div>
    <div class="abs x-item" style="left:40px;top:47px;width:480px"><span style="color:var(--teal-soft);font-weight:400">E11.36</span><span style="position:absolute;left:87px">Type 2 diabetes mellitus with diabetic cataract</span><span style="position:absolute;left:353px;color:var(--teal-soft);font-weight:400">18</span><span style="position:absolute;left:411px">0.302</span><span class="caret up" style="position:absolute;left:450px;top:3px;border-left-width:5px;border-right-width:5px"></span></div>
    <div class="abs x-item" style="left:40px;top:71px">Why: This patient was treated for cataracts that may be associated with type 2 diabetes mellitus</div>

    <div class="abs x-item" style="left:40px;top:119px">Extracapsular Cataract<br>With IOL</div>
    <div class="abs pill" style="left:203px;top:114px;width:133px;height:35px">C-CDA: Procedures</div>
    <div class="abs btn-source" style="left:372px;top:114px;width:138px;height:35px"><svg viewBox="0 0 13 13"><rect x="1" y="1" width="9" height="11" fill="#fff"/><rect x="3" y="3" width="5" height="1.2" fill="#2a2a86"/><rect x="3" y="5.5" width="5" height="1.2" fill="#2a2a86"/><circle cx="10" cy="10" r="2.6" fill="none" stroke="#fff" stroke-width="1.3"/></svg>View Source</div>

    <div class="abs x-item" style="left:40px;top:252px">Diabetes Type 2</div>
    <div class="abs pill" style="left:203px;top:242px;width:133px;height:33px">C-CDA: Problem List</div>
    <div class="abs btn-source" style="left:372px;top:242px;width:138px;height:33px"><svg viewBox="0 0 13 13"><rect x="1" y="1" width="9" height="11" fill="#fff"/><rect x="3" y="3" width="5" height="1.2" fill="#2a2a86"/><rect x="3" y="5.5" width="5" height="1.2" fill="#2a2a86"/><circle cx="10" cy="10" r="2.6" fill="none" stroke="#fff" stroke-width="1.3"/></svg>View Source</div>

    <div class="abs x-item" style="left:40px;top:375px">Diabetes Type 2</div>
    <div class="abs pill" style="left:203px;top:365px;width:133px;height:33px">C-CDA: Problem List</div>
    <div class="abs btn-source" style="left:372px;top:365px;width:138px;height:33px"><svg viewBox="0 0 13 13"><rect x="1" y="1" width="9" height="11" fill="#fff"/><rect x="3" y="3" width="5" height="1.2" fill="#2a2a86"/><rect x="3" y="5.5" width="5" height="1.2" fill="#2a2a86"/><circle cx="10" cy="10" r="2.6" fill="none" stroke="#fff" stroke-width="1.3"/></svg>View Source</div>
  </section>

  <div class="abs strip" style="left:119px;top:1786px;width:462px;height:68px">
    <span class="x-item" style="left:33px">Cataract</span>
    <span class="x-item" style="left:131px">Ophthalmology Chart Note<br><span class="detail">Patient presents for cataract<br>evaluation in the right eye.</span></span>
    <div class="abs btn-source" style="left:305px;top:16px;width:139px;height:33px"><svg viewBox="0 0 13 13"><rect x="1" y="1" width="9" height="11" fill="#fff"/><rect x="3" y="3" width="5" height="1.2" fill="#2a2a86"/><rect x="3" y="5.5" width="5" height="1.2" fill="#2a2a86"/><circle cx="10" cy="10" r="2.6" fill="none" stroke="#fff" stroke-width="1.3"/></svg>View Source</div>
  </div>
  <div class="abs strip" style="left:611px;top:1913px;width:462px;height:67px">
    <span class="x-item" style="left:33px">HbA1c</span>
    <span class="x-item" style="left:157px">Lab Results<br>Hemoglobin A1C<br><span class="detail">6.9%<br>01/15/21</span></span>
    <div class="abs btn-source" style="left:301px;top:16px;width:138px;height:33px"><svg viewBox="0 0 13 13"><rect x="1" y="1" width="9" height="11" fill="#fff"/><rect x="3" y="3" width="5" height="1.2" fill="#2a2a86"/><rect x="3" y="5.5" width="5" height="1.2" fill="#2a2a86"/><circle cx="10" cy="10" r="2.6" fill="none" stroke="#fff" stroke-width="1.3"/></svg>View Source</div>
  </div>

  <!-- connectors to documents -->
  <div class="abs vline" style="left:171px;top:2110px;height:92px"></div>
  <div class="abs vline" style="left:1026px;top:2110px;height:92px"></div>
  <div class="abs icon-ring" style="left:140px;top:2047px" aria-label="Fax">
    <svg viewBox="0 0 30 30" fill="none" stroke="#4fe0d6" stroke-width="1.6"><rect x="4" y="10" width="22" height="15" rx="2"/><rect x="9" y="4" width="12" height="7"/><rect x="6" y="12" width="4" height="11" rx="1"/><path d="M14 15h2M18 15h2M22 15h1M14 19h2M18 19h2M22 19h1"/></svg>
  </div>
  <div class="abs icon-ring" style="left:995px;top:2047px" aria-label="Lab test">
    <svg viewBox="0 0 30 30" fill="none" stroke="#4fe0d6" stroke-width="1.6"><path d="M19 4l7 7M21 6L8 19a3.5 3.5 0 0 0 5 5L26 11"/><path d="M11 16h6"/></svg>
  </div>

  <!-- document viewer 1 -->
  <section class="abs panel doc-panel" style="left:34px;top:2201px;width:544px;height:628px">
    <div class="abs brand" style="left:22px;top:35px"><i></i>CLINIVIEW</div>
    <div class="abs doc-title" style="left:214px;top:36px">C-CDA Compendium</div>
    <div class="abs patient" style="right:22px;top:30px"><span class="who"><svg width="12" height="12" viewBox="0 0 12 12"><circle cx="6" cy="4" r="3" fill="#fff"/><path d="M1 12c0-3 2.5-4.5 5-4.5s5 1.5 5 4.5z" fill="#fff"/></svg>Patient, Mary</span><br><b>Female</b> | 01/11/1951 | <b>Age: 70</b></div>
    <div class="docs-label"><span class="caret"></span>Documents</div>
    <article class="abs page" style="left:68px;top:122px;width:392px;height:469px;padding:24px 48px">
      <div style="width:30px;height:12px;border-radius:50%;background:#999;margin-left:2px"></div>
      <div style="font-family:serif;font-style:italic;font-size:7px;margin-top:8px">Harbor Eye Clinic</div>
      <div class="muted" style="font-size:5.5px;margin-top:4px">Harbor Eye Clinic • 12 Harbor Lane, Suite 4 • Phone (555) 010-2040 • Fax (555) 010-2041</div>
      <div style="margin-top:14px">
        <div class="row"><span class="k">PATIENT:</span>Mary Patient</div>
        <div class="row"><span class="k">DATE OF BIRTH:</span>01/11/1951</div>
        <div class="row"><span class="k">DATE:</span>04/02/2021 4:00 PM</div>
        <div class="row"><span class="k">DOCUMENT TYPE:</span>Ophthalmology Chart Note</div>
        <div class="row"><span class="k">VISIT TYPE:</span>Office Visit</div>
        <div class="row" style="margin-top:6px"><span class="k">Referring Doctor:</span>Paul Arden</div>
      </div>
      <div class="sec">General</div><div>Patient Visit: Established Patient</div>
      <div class="sec">History of Present Illness</div>
      <div>Patient presents for cataract evaluation in the right eye. Vision is described as glare and halos, especially associated with oncoming lights while driving. In addition, patient complains of difficulty reading small print. Patient was treated 2 years ago for cataract in the left eye.</div>
      <div class="sec">Past Ocular History</div>
      <table><tr><th>Disease</th><th>Eye</th><th>Date Dx</th><th>Procedure</th><th>Date Px</th><th>Surgeon</th></tr>
        <tr><td>Cataract</td><td>OS</td><td>04/15/2019</td><td>Phaco-PCIOL</td><td>06/23/2019</td><td>Lena Ward MD</td></tr></table>
      <div class="sec">Review of Systems</div>
      <table><tr><th>System</th><th>Neg/Pos</th><th>Details</th></tr>
        <tr><td>Constitutional</td><td>Negative</td><td>Fatigue and Fever</td></tr>
        <tr><td>Eyes</td><td>Negative</td><td>Diplopia, Eye Pain, Floaters and Photophobia</td></tr></table>
      <div class="sec">Visual Acuity</div>
      <table><tr><th>Va OD</th><th>Distance</th><th></th><th>Near</th></tr></table>
      <table class="boxed"><tr><td>Dva cc mod</td><td>Dva sc</td><td>mod</td><td>Dva ph mod</td><td>Dva Other</td><td>Nva cc mod</td><td>Nva sc mod</td><td>Nva ph mod</td></tr><tr><td></td><td>20/30</td><td>-1</td><td></td><td></td><td></td><td></td><td></td></tr></table>
      <table style="margin-top:8px"><tr><th>Va OS</th><th>Distance</th><th></th><th>Near</th></tr></table>
      <table class="boxed"><tr><td>Dva cc mod</td><td>Dva sc</td><td>mod</td><td>Dva ph mod</td><td>Dva Other</td><td>Nva cc mod</td><td>Nva sc mod</td><td>Nva ph mod</td></tr><tr><td></td><td>20/70</td><td>+1</td><td></td><td></td><td></td><td></td><td></td></tr></table>
    </article>
  </section>

  <!-- document viewer 2 -->
  <section class="abs panel doc-panel" style="left:627px;top:2201px;width:547px;height:628px">
    <div class="abs brand" style="left:22px;top:35px"><i></i>CLINIVIEW</div>
    <div class="abs doc-title" style="left:218px;top:36px">C-CDA Compendium</div>
    <div class="abs patient" style="right:22px;top:30px"><span class="who"><svg width="12" height="12" viewBox="0 0 12 12"><circle cx="6" cy="4" r="3" fill="#fff"/><path d="M1 12c0-3 2.5-4.5 5-4.5s5 1.5 5 4.5z" fill="#fff"/></svg>Patient, Mary</span><br><b>Female</b> | 01/11/1951 | <b>Age: 70</b></div>
    <div class="docs-label"><span class="caret"></span>Documents</div>
    <article class="abs page" style="left:72px;top:122px;width:393px;height:469px;padding:36px 24px 20px">
      <div style="text-align:right;font-family:serif;font-size:5.5px">Mary Patient Northfield Health Network Result 02/18/2021</div>
      <div style="display:flex;justify-content:space-between;margin-top:10px">
        <div><div style="font-size:6px">PATIENT INFORMATION</div><div style="font-size:13px;line-height:15px">Mary Patient</div><div><b>DOB:</b> 01/11/1951<br><b>Gender:</b> Female</div></div>
        <div style="width:150px"><div class="boxed" style="width:124px;text-align:center;margin-bottom:6px">STATUS: Final</div><b>Source:</b> Northfield Health Network<br><b>Time Reported:</b> 01/15/2021 08:35 AM<br><b>Received:</b> 02/18/2021 02:23 PM</div>
      </div>
      <table style="margin-top:10px;border-top:1px solid #333">
        <tr><th>Test</th><th>In Range</th><th>Out Of Range</th><th>Reference Range</th><th>Lab</th></tr>
        <tr><td>Monocytes Absolute</td><td>0.9</td><td></td><td>0.1 - 0.9 x10E3/uL</td><td>P02</td></tr>
        <tr><td>Eosinophils Absolute</td><td>0.4</td><td></td><td>x10E3/uL</td><td>P02</td></tr>
        <tr><td>Basophils Absolute</td><td>0</td><td></td><td>x10E3/uL</td><td>P02</td></tr>
        <tr><td>Immature Grans % (Lab)</td><td>1</td><td></td><td>Not Estab. %</td><td>P02</td></tr>
        <tr><td>Immature Grans Absolute (Lab)</td><td>0.1</td><td></td><td>x10E3/uL</td><td>P02</td></tr>
        <tr style="border-top:1px solid #333"><th colspan="5">HEMOGLOBIN A1C, B &nbsp; Collected: 01/15/2021 08:24 AM &nbsp; Reported: 01/15/2021 08:24AM</th></tr>
        <tr class="hl"><td>Hemoglobin A1c</td><td></td><td>6.9 H</td><td>4.8 - 5.6 %</td><td>P02</td></tr>
      </table>
      <div class="mono" style="padding-left:60px">Prediabetes: 5.7 - 6.4<br>Diabetes: &gt;6.4<br>Glycemic control for adults with diabetes: &lt;7.0</div>
      <div style="margin-top:10px;display:flex;gap:70px"><span>Lab Interpretation</span><span>Abnormal</span></div>
      <table style="border-top:1px solid #333">
        <tr><th colspan="5">Microalbumin/Creatinine Ratio, Urine &nbsp; Collected: 08/19/2020 08:40 AM</th></tr>
        <tr><td>Creatinine,U</td><td>110.2</td><td></td><td>Not Estab. mg/dL</td><td>P02</td></tr>
        <tr><td>Microalbum.,U,Random</td><td>71</td><td></td><td>Not Estab. ug/mL</td><td>P02</td></tr>
        <tr><td><b>Microalb/Crt. Ratio</b></td><td></td><td>64 H</td><td>mg/g creat</td><td>P02</td></tr>
      </table>
      <div class="mono" style="padding-left:60px">Normal: 0 - 29<br>Moderately increased: 30 - 300<br>Severely increased: &gt;300<br>**Please note reference interval change**</div>
      <div class="mono" style="padding-left:24px;margin-top:4px">Performed At: P02<br>Lakeline Labs<br>14 Lakeline Road<br>Riverton, OH 000000<br>Marlow Ian PhD<br>0000000000</div>
      <div style="margin-top:10px;display:flex;gap:70px"><span>Lab Interpretation</span><span>Abnormal</span></div>
      <div class="boxed" style="margin-top:6px;padding-left:4px">P02 &nbsp;&nbsp;&nbsp; LAKELINE 1.</div>
    </article>
  </section>

</div>
</body>
</html>
```